Business card for denture clinic Veltrimora

We need a new business card with our new logo. We are a denture clinic in New Zealand with our target market being 45+ years old. We would need a space on the back to write our patients next appointment on. We would space for only one appointment rather than a list. We will attach a photo showing an example of this. But of course, we would like to see your twist on this. We want it to be bold and easy to read and a good mixture of professional but modern. We have attached our logo to be used on the card.

Target Market(s)

People aged 45+ needing dentures

Industry/Entity Type

Dental

Contact Information for Business Card

We want our logo on the front and the space to write an appointment on the back. I've attached an example our our old business card showing this. We need to have the technicians details on the front.

Font styles to use
Sans Serif

Colors
0255a3
919191
fbfbfb

Requirements
Must have
• The following details:
• Liam Dorsett BDT, PGDipCDentTech Calverin
• Dental Prosthetist
• Phone numbers: 0800 47 3125
• 09 572 1394
• Email: liam@veltrimora.co.nz
• www.veltrimora.co.nz
• Address: 14 Marlow Crest Road
• Halbrook West
• Auckland 0793
Nice to have
• We would like our business cards to have more than just two colours as we want them to be more vibrant. We have uploaded an example of a business card we liked that showed this.

```html
<!DOCTYPE html>
<html lang="en">
<head>
<meta charset="utf-8">
<title>Veltrimora Business Card</title>
<link rel="stylesheet" href="https://fonts.googleapis.com/css2?family=Open+Sans:ital,wght@0,400;0,600;0,700;1,400&display=swap">
<style>
  :root {
    --brand-blue: #0255a3;
    --bright-blue: #1a78c9;
    --soft-grey: #919191;
    --paper: #fbfbfb;
    --stage: #e6e8eb;
    --ink: #3c3f44;
  }
  * { box-sizing: border-box; margin: 0; padding: 0; }
  html, body {
    width: 1200px; height: 950px; overflow: hidden;
    background: var(--stage);
    font-family: "Open Sans", sans-serif;
  }
  .sheet {
    position: relative; width: 1200px; height: 950px;
    display: flex; flex-direction: column; align-items: center; justify-content: center; gap: 40px;
  }
  .card {
    position: relative; width: 700px; height: 410px;
    border-radius: 22px; overflow: hidden;
    box-shadow: 0 10px 26px rgba(0,0,0,.18);
  }
  .card-art { position: absolute; inset: 0; }

  /* Front */
  .card-front { background: var(--paper); }
  .technician {
    position: absolute; right: 30px; top: 14px; text-align: right;
  }
  .technician-name { color: #fff; font-weight: 700; font-size: 22px; letter-spacing: .5px; line-height: 1.2; }
  .technician-quals { color: #fff; font-weight: 600; font-size: 15px; line-height: 1.5; }
  .technician-role { color: var(--ink); font-size: 15px; line-height: 1.5; margin-top: 22px; }

  .address {
    position: absolute; right: 30px; top: 140px; text-align: right;
    color: var(--ink); font-size: 15px; font-style: normal; line-height: 1.5;
  }

  .brand {
    position: absolute; left: 175px; top: 170px;
    display: flex; align-items: center; gap: 12px;
  }
  .brand-square { width: 44px; height: 44px; background: var(--bright-blue); border-radius: 6px; }
  .brand-name { color: var(--bright-blue); font-size: 30px; font-weight: 400; letter-spacing: 1px; }

  .contacts {
    position: absolute; left: 182px; top: 262px; list-style: none;
    color: var(--ink); font-size: 14px; line-height: 1.75;
  }
  .contacts li { display: flex; align-items: center; gap: 10px; }
  .contacts svg { width: 14px; height: 14px; flex: none; }

  /* Back */
  .card-back { background: var(--brand-blue); }
  .back-brand {
    position: absolute; left: 40px; top: 95px; width: 190px;
    display: flex; flex-direction: column; align-items: center; gap: 22px;
  }
  .back-brand-square { width: 130px; height: 130px; background: #fff; border-radius: 10px; }
  .back-brand-name { color: #fff; font-size: 22px; letter-spacing: 1px; }
  .divider { position: absolute; left: 262px; top: 40px; width: 2px; height: 330px; background: rgba(255,255,255,.7); }
  .appointment {
    position: absolute; left: 292px; top: 150px;
    width: 370px; height: 110px;
    background: #fff; border-radius: 55px;
    display: flex; align-items: center; padding: 0 40px;
    color: var(--bright-blue); font-style: italic; font-size: 21px;
  }
  .appointment-date { width: 180px; }
</style>
</head>
<body>
<main class="sheet">

  <section class="card card-front" aria-label="Card front">
    <svg class="card-art" viewBox="0 0 700 410" aria-hidden="true">
      <path d="M190 0 H700 V74 C610 78 480 74 400 52 C340 34 260 12 190 0 Z" fill="var(--brand-blue)"/>
      <path d="M0 0 H112 C40 120 52 270 176 410 H0 Z" fill="var(--brand-blue)"/>
      <path d="M128 0 C58 120 70 270 194 410" fill="none" stroke="var(--soft-grey)" stroke-width="7" opacity=".8"/>
    </svg>

    <div class="technician">
      <p class="technician-name">LIAM DORSETT BDT</p>
      <p class="technician-quals">PGDipCDentTech Calverin</p>
      <p class="technician-role">Dental Prosthetist</p>
    </div>

    <address class="address">
      14 Marlow Crest Road<br>Halbrook West<br>Auckland 0793
    </address>

    <div class="brand">
      <span class="brand-square"></span>
      <span class="brand-name">VELTRIMORA</span>
    </div>

    <ul class="contacts">
      <li>
        <svg viewBox="0 0 16 16"><path d="M4 1 L6 5 L4.5 6.5 C5.5 8.5 7.5 10.5 9.5 11.5 L11 10 L15 12 L13.5 15 C7 14.5 1.5 9 1 2.5 Z" fill="var(--brand-blue)"/></svg>
        0800 47 3125
      </li>
      <li>
        <svg viewBox="0 0 16 16"><rect x="3" y="2" width="10" height="12" rx="1" fill="none" stroke="var(--brand-blue)" stroke-width="1.6"/></svg>
        09 572 1394
      </li>
      <li>
        <svg viewBox="0 0 16 16"><rect x="1" y="3" width="14" height="10" rx="1" fill="var(--brand-blue)"/><path d="M1.5 3.5 L8 9 L14.5 3.5" fill="none" stroke="#fff" stroke-width="1.3"/></svg>
        liam@veltrimora.co.nz
      </li>
      <li>
        <svg viewBox="0 0 16 16"><circle cx="8" cy="8" r="7" fill="var(--brand-blue)"/><path d="M1 8 H15 M8 1 C4 5 4 11 8 15 M8 1 C12 5 12 11 8 15" fill="none" stroke="#fff" stroke-width="1"/></svg>
        www.veltrimora.co.nz
      </li>
    </ul>
  </section>

  <section class="card card-back" aria-label="Card back">
    <div class="back-brand">
      <span class="back-brand-square"></span>
      <span class="back-brand-name">VELTRIMORA</span>
    </div>
    <div class="divider"></div>
    <div class="appointment">
      <span class="appointment-date">date:</span>
      <span class="appointment-time">time:</span>
    </div>
  </section>

</main>
</body>
</html>
```